Oil and Gas Exploration and Production company needs a business card design

We need a business card design using our logo and colors in the logo. We want a mainstream design.

```html
<!DOCTYPE html>
<html lang="en">
<head>
<meta charset="utf-8">
<title>Solara Oil &amp; Gas — Business Card</title>
<link rel="stylesheet" href="https://fonts.googleapis.com/css2?family=Roboto+Slab:wght@900&family=Crimson+Text:wght@700&family=Open+Sans:wght@400&display=swap">
<style>
  :root {
    --backdrop: #f1ebdc;
    --gold: #c8982f;
    --gold-soft: #d3a84a;
    --cream: #f0e2a2;
    --white: #ffffff;
    --ink: #0c0c0c;
  }
  * { box-sizing: border-box; margin: 0; padding: 0; }
  html, body { width: 1200px; height: 982px; overflow: hidden; }
  body {
    background: var(--backdrop);
    position: relative;
  }
  .card {
    position: absolute;
    left: 100px;
    top: 171px;
    width: 1000px;
    height: 640px;
    background: var(--gold);
    overflow: hidden;
  }
  .card__glow {
    position: absolute;
    left: 290px;
    top: 10px;
    width: 560px;
    height: 560px;
    border-radius: 50%;
    background: var(--gold-soft);
    opacity: 0.45;
  }
  .brand {
    position: absolute;
    top: 110px;
    left: 0;
    width: 100%;
    text-align: center;
  }
  .brand__mark {
    display: inline-flex;
    align-items: center;
    gap: 22px;
  }
  .brand__dot {
    width: 70px;
    height: 70px;
    border-radius: 50%;
    background: var(--ink);
  }
  .brand__name {
    font-family: "Roboto Slab", serif;
    font-weight: 900;
    font-size: 150px;
    line-height: 1;
    color: var(--ink);
    letter-spacing: -2px;
  }
  .brand__tag {
    margin-top: 14px;
    margin-left: 90px;
    font-family: "Crimson Text", serif;
    font-weight: 700;
    font-size: 54px;
    letter-spacing: 9px;
    color: var(--white);
    line-height: 1;
  }
  .person {
    position: absolute;
    top: 378px;
    left: 0;
    width: 100%;
    text-align: center;
    padding-left: 70px;
  }
  .person__name {
    font-family: "Crimson Text", serif;
    font-weight: 700;
    font-size: 42px;
    color: var(--white);
    line-height: 1.1;
  }
  .person__title {
    font-family: "Open Sans", sans-serif;
    font-size: 32px;
    color: var(--ink);
    line-height: 1.2;
  }
  .card__curve {
    position: absolute;
    left: 0;
    top: 490px;
    width: 1000px;
    height: 40px;
  }
  .contact {
    position: absolute;
    left: 0;
    top: 516px;
    width: 100%;
    height: 58px;
    background: var(--white);
    display: flex;
    align-items: center;
    justify-content: center;
    font-family: "Open Sans", sans-serif;
    font-size: 30px;
    color: var(--ink);
    padding-left: 80px;
  }
  .contact__sep { margin: 0 8px; }
  .web {
    position: absolute;
    left: 0;
    top: 574px;
    width: 100%;
    height: 66px;
    background: var(--ink);
    display: flex;
    align-items: center;
    justify-content: center;
    font-family: "Open Sans", sans-serif;
    font-size: 31px;
    color: var(--white);
    padding-left: 10px;
  }
</style>
</head>
<body>
  <div class="card">
    <div class="card__glow"></div>

    <div class="brand">
      <div class="brand__mark">
        <span class="brand__dot"></span>
        <span class="brand__name">Solara</span>
      </div>
      <div class="brand__tag">OIL &amp; GAS</div>
    </div>

    <div class="person">
      <div class="person__name">Your Name</div>
      <div class="person__title">OWNER</div>
    </div>

    <svg class="card__curve" viewBox="0 0 1000 40" preserveAspectRatio="none" aria-hidden="true">
      <path d="M0 26 Q500 -8 1000 26 L1000 40 L0 40 Z" fill="var(--cream)"/>
    </svg>

    <div class="contact">
      <span>(555) 010-2040</span><span class="contact__sep">|</span><span>info@solara-oilandgas.com</span>
    </div>
    <div class="web">www.solara-oilandgas.com</div>
  </div>
</body>
</html>
```